School Poster and Prompt Design

I would like posters created for each of our school values (from the attached Way of Working document). In these posters I would like our logo, and some graphics or pictures - you can use the strategic plan attached for some examples.

I would also like a Code of Conduct Prompt for teachers and students (smaller design that can be used as a sticker for a laptop) based on the attached Tallowmere Heights Basics document. I have also attached a photo example, which we quite like that can be used for a base. This document is called example classroom management prompts.

Target Market(s)

School and students

Requirements
Must have
• Logo built into the design
Our school motto at the bottom 'Strive to Accomplish'
Design that incorporates elements that relate to each of the values.
Design that looks and feels like the example. In our school colours.
Nice to have
• Posters - Easy to read and understand from a distance.
Prompt - Easy to read and understand if turned into a sticker for a laptop.

```html
<!DOCTYPE html>
<html lang="en">
<head>
<meta charset="utf-8">
<title>Tallowmere Heights Basics – Student Focus</title>
<link href="https://fonts.googleapis.com/css2?family=Arimo:wght@400;700&display=swap" rel="stylesheet">
<style>
:root{
  --navy:#14173f;
  --royal:#04518f;
  --deep:#0a4f91;
  --mid:#1e88c8;
  --sky:#29bdee;
  --cyan:#29b5e8;
  --link:#1d7fc1;
  --white:#ffffff;
  --wall:#e4e5e7;
}
*{box-sizing:border-box;margin:0;padding:0}
html,body{width:1019px;height:1200px;overflow:hidden;background:var(--wall);font-family:"Arimo",Arial,sans-serif}
.poster{position:absolute;left:88px;top:5px;width:842px;height:1190px;background:var(--white);overflow:hidden}
.abs{position:absolute}
.center{text-align:center}
.header{left:0;top:22px;width:842px;height:166px;background:linear-gradient(90deg,var(--royal) 0%,#1a2a6a 30%,var(--navy) 60%)}
.title{left:200px;top:42px;width:584px;color:var(--white);font-size:33px;letter-spacing:1.5px;text-align:center}
.subtitle{left:200px;top:88px;width:584px;color:var(--cyan);font-size:32px;text-align:center}
.brand{left:30px;top:40px;width:200px;display:flex;align-items:center;gap:10px}
.brand-dot{width:34px;height:34px;border-radius:50%;background:var(--sky);flex:none}
.brand-name{color:var(--white);font-size:20px;font-weight:700;line-height:1.15}
.motto{left:0;top:201px;width:842px;color:var(--link);font-size:19px}
.entry{left:27px;top:240px;width:788px;height:237px;background:var(--mid)}
.pointer-down{width:0;height:0;border-left:14px solid transparent;border-right:14px solid transparent}
.entry-pointer{left:407px;top:240px;border-top:14px solid var(--white)}
.entry-title{left:0;top:22px;width:788px;color:var(--white);font-size:50px;font-weight:700}
.value{top:79px;width:230px;height:140px;color:var(--white);padding:33px 0 0 34px}
.value h3{font-size:16px;letter-spacing:1.2px;font-weight:700;margin-bottom:9px}
.value ul{list-style:none;font-size:13px;line-height:19px}
.value li::before{content:"•";margin-right:10px}
.value.light{background:var(--sky)}
.value.dark{background:var(--deep);padding-left:50px}
.lesson{left:22px;top:496px;width:795px;height:219px;border:3px dotted var(--link)}
.lesson-title{left:0;top:28px;width:789px;color:var(--deep);font-size:42px;font-weight:700;letter-spacing:1px}
.lesson-sub{left:0;top:85px;width:789px;color:var(--link);font-size:16px}
.item{width:260px;font-size:16px;line-height:19px;text-transform:uppercase}
.item svg{display:block;margin:0 auto 4px}
.lesson .item{color:var(--deep);top:125px}
.exit{left:0;top:742px;width:842px;height:221px;background:var(--royal)}
.exit-title{left:0;top:16px;width:842px;color:var(--white);font-size:52px;font-weight:700}
.exit-sub{left:0;top:78px;width:842px;color:var(--cyan);font-size:27px;letter-spacing:.5px}
.exit .item{color:var(--white);top:126px;line-height:21px}
.exit-pointer{left:407px;top:963px;border-top:16px solid var(--royal)}
.always{left:2px;top:998px;width:840px;height:44px;background:linear-gradient(90deg,var(--sky),var(--mid) 45%,var(--royal));color:var(--white);font-size:19px;line-height:44px}
.icon{top:1048px;height:64px;border-radius:6px;background:linear-gradient(180deg,var(--mid),var(--deep))}
.rule{top:1125px;width:260px;color:var(--deep);font-size:14px;line-height:17px}
</style>
</head>
<body>
<main class="poster">
  <div class="abs header"></div>
  <div class="abs brand"><span class="brand-dot"></span><span class="brand-name">Tallowmere Heights High School</span></div>
  <h1 class="abs title">TALLOWMERE HEIGHTS BASICS</h1>
  <h2 class="abs subtitle" style="font-weight:400">STUDENT FOCUS</h2>

  <p class="abs motto center">STRIVE TO ACCOMPLISH</p>

  <section class="abs entry">
    <h2 class="abs entry-title center">ENTRY</h2>
    <div class="abs value light" style="left:21px"><h3>COMMITMENT</h3><ul><li>On time</li><li>Correct uniform</li><li>Ready to learning</li></ul></div>
    <div class="abs value dark" style="left:278px"><h3>COURTESY</h3><ul><li>In line</li><li>Waiting quietly</li><li>Stand behind chairs</li></ul></div>
    <div class="abs value light" style="left:534px;padding-left:47px"><h3>COOPERATION</h3><ul><li>In the right seat</li><li>Ready to participate</li><li>Actively listening</li></ul></div>
  </section>
  <div class="abs pointer-down entry-pointer"></div>

  <section class="abs lesson">
    <h2 class="abs lesson-title center">DURING THE LESSON</h2>
    <p class="abs lesson-sub center">SHOW AND EXPLAIN TO STUDENTS</p>
    <div class="abs item center" style="left:17px"><svg width="30" height="26" viewBox="0 0 30 26"><circle cx="12" cy="14" r="10" fill="none" stroke="#1d7fc1" stroke-width="2"/><path d="M7 14l5 5L27 2" fill="none" stroke="#29bdee" stroke-width="3"/></svg>Address all staff<br>appropriately</div>
    <div class="abs item center" style="left:265px"><svg width="30" height="26" viewBox="0 0 30 26"><circle cx="12" cy="14" r="10" fill="none" stroke="#1d7fc1" stroke-width="2"/><path d="M7 14l5 5L27 2" fill="none" stroke="#29bdee" stroke-width="3"/></svg>Display good<br>manners</div>
    <div class="abs item center" style="left:522px"><svg width="30" height="26" viewBox="0 0 30 26"><circle cx="12" cy="14" r="10" fill="none" stroke="#1d7fc1" stroke-width="2"/><path d="M7 14l5 5L27 2" fill="none" stroke="#29bdee" stroke-width="3"/></svg>Complete all<br>set work</div>
  </section>

  <section class="abs exit">
    <h2 class="abs exit-title center">EXIT</h2>
    <p class="abs exit-sub center">BEFORE YOU LEAVE…</p>
    <div class="abs item center" style="left:37px"><svg width="30" height="26" viewBox="0 0 30 26"><circle cx="12" cy="14" r="10" fill="none" stroke="#29bdee" stroke-width="2"/><path d="M7 14l5 5L27 2" fill="none" stroke="#29bdee" stroke-width="3"/></svg>Technology<br>is checked</div>
    <div class="abs item center" style="left:291px"><svg width="30" height="26" viewBox="0 0 30 26"><circle cx="12" cy="14" r="10" fill="none" stroke="#29bdee" stroke-width="2"/><path d="M7 14l5 5L27 2" fill="none" stroke="#29bdee" stroke-width="3"/></svg>Environment left<br>neat and tidy</div>
    <div class="abs item center" style="left:567px"><svg width="30" height="26" viewBox="0 0 30 26"><circle cx="12" cy="14" r="10" fill="none" stroke="#29bdee" stroke-width="2"/><path d="M7 14l5 5L27 2" fill="none" stroke="#29bdee" stroke-width="3"/></svg>Homework is<br>in planner</div>
  </section>
  <div class="abs pointer-down exit-pointer"></div>

  <p class="abs always center">ENSURE THAT YOU ALWAYS</p>

  <div class="abs icon" style="left:130px;width:76px" role="img" aria-label="Icon of two people resolving a problem peacefully"></div>
  <div class="abs icon" style="left:390px;width:64px" role="img" aria-label="Icon of a group of people"></div>
  <div class="abs icon" style="left:680px;width:36px" role="img" aria-label="Icon of a hand holding a mobile phone"></div>

  <p class="abs rule center" style="left:36px">Resolve all problems peacefully<br>without violence or abuse</p>
  <p class="abs rule center" style="left:292px">Wait to be invited to<br>enter or exit the classroom</p>
  <p class="abs rule center" style="left:567px">Never use a personal mobile<br>phone or electronic device</p>
</main>
</body>
</html>
```